Sports hypnotherapist needs electronic letterhead design

Need a simple but classy design for a letterhead that looks good when printed. Its for a hypnotherapist who specialises in elite sport. Should have my company name and address and website details on it. I specialise in footballers.
Should look good electronically and when printed.
Include all contact details as shown in the must haves.

Target Market(s)

Sports people, elite sport.

Industry/Entity Type

Hypnotherapy

Font styles to use
Sans Serif

Colors

Designer to choose colors to be used in the design.

Requirements
Must have
• NEEDS TO BE DESIGNED IN MS WORD
• Logo +
• Calm Summit Hypnotherapists
• 27 Marlow Rise
• Bracknell
• SN7 4LT
• Tel: 07815 264731
• E: calmsummitcoaching@examplemail.co.uk
• www: http://www.calm-summit.co.uk.
• Derek Moss
• Clinical hypnotherapist, hypnoanalyst, mental resilience coach, MSc, Dip PHH
Nice to have
• A watermark?
• Plenty of space for the A4 letter
• Prints well.
Should not have
• Too much clutter.
• Too much colour that will be costly to print.

```html
<!DOCTYPE html>
<html lang="en">
<head>
<meta charset="utf-8">
<title>Calm Summit Hypnotherapists – Letterhead</title>
<link rel="stylesheet" href="https://fonts.googleapis.com/css2?family=Open+Sans:wght@400;600;700&family=Roboto:wght@500;700&display=swap">
<style>
  :root {
    --paper: #fafafa;
    --accent: #5ab4e5;
    --ink: #222222;
    --text: #555555;
    --muted: #666666;
    --watermark-grey: #e6e6e6;
    --watermark-blue: #eaf3fa;
  }
  * { margin: 0; padding: 0; box-sizing: border-box; }
  html, body { width: 1102px; height: 1200px; overflow: hidden; background: var(--paper); }
  .letterhead {
    position: relative; width: 1102px; height: 1200px;
    background: var(--paper); font-family: "Open Sans", sans-serif; color: var(--text);
  }
  .brand {
    position: absolute; left: 73px; top: 92px;
    display: flex; align-items: center; gap: 14px;
  }
  .brand-dot { width: 30px; height: 30px; border-radius: 50%; background: var(--accent); }
  .brand-name { font-weight: 700; font-size: 38px; color: var(--ink); letter-spacing: -0.5px; }

  .contact { position: absolute; right: 75px; top: 82px; text-align: right; }
  .company-name {
    font-family: "Roboto", sans-serif; font-weight: 700; font-size: 21px;
    color: var(--accent); margin-bottom: 6px;
  }
  .contact-line {
    font-size: 14.5px; color: var(--ink); line-height: 17px;
    display: flex; justify-content: flex-end; align-items: center; gap: 6px;
  }
  .contact-line .hl { color: var(--accent); }
  .contact-line svg { width: 11px; height: 11px; fill: var(--accent); flex: none; }

  .tab { position: absolute; background: var(--accent); }
  .tab-top { right: 0; top: 64px; width: 20px; height: 102px; border-radius: 18px 0 0 18px; }
  .tab-bottom { left: 0; top: 1090px; width: 19px; height: 76px; border-radius: 0 18px 18px 0; }

  .watermark {
    position: absolute; left: 490px; top: 629px; width: 584px; height: 551px;
    background: radial-gradient(ellipse at 70% 40%, var(--watermark-grey) 0%, var(--watermark-blue) 55%, rgba(250,250,250,0) 80%);
    border-radius: 40% 40% 0 0;
  }

  .letter { position: absolute; left: 109px; top: 314px; width: 883px; font-size: 15px; line-height: 22px; }
  .salutation { margin-bottom: 43px; }
  .letter p.body { text-align: justify; margin-bottom: 20px; }

  .sign-off { position: absolute; left: 109px; top: 830px; }
  .sign-name { font-weight: 700; font-size: 14.5px; color: var(--muted); }
  .signature {
    width: 265px; height: 46px; margin: 14px 0 12px;
    background: linear-gradient(90deg, #d6e9f6, #e8f2fa);
    border-radius: 4px;
  }
  .sign-role { font-size: 14.5px; color: var(--muted); }

  .practitioner { position: absolute; left: 55px; top: 1106px; }
  .practitioner-name {
    font-family: "Roboto", sans-serif; font-weight: 500; font-size: 20px; color: var(--accent);
  }
  .credentials { font-size: 14.5px; color: var(--ink); margin-top: 4px; }
  .credentials .sep { color: var(--accent); margin: 0 7px; }

  .base-band { position: absolute; left: 0; bottom: 0; }
</style>
</head>
<body>
<main class="letterhead">
  <div class="brand">
    <span class="brand-dot"></span>
    <span class="brand-name">Calm Summit</span>
  </div>

  <div class="contact">
    <div class="company-name">Calm Summit Hypnotherapists</div>
    <div class="contact-line">07815 264731
      <svg viewBox="0 0 12 12" aria-hidden="true"><path d="M2.5 1l2 2-1 1.5a7 7 0 0 0 4 4l1.5-1 2 2-1.5 1.5C5 11 1 7 1 2.5z"/></svg>
      www.<span class="hl">calm-summit</span>.co.uk
      <svg viewBox="0 0 12 12" aria-hidden="true"><circle cx="6" cy="6" r="5"/></svg>
    </div>
    <div class="contact-line">calmsummitcoaching@examplemail.co.uk
      <svg viewBox="0 0 12 12" aria-hidden="true"><path d="M1 3h10v7H1z M1 3l5 4 5-4" /></svg>
    </div>
    <div class="contact-line">27 Marlow Rise Bracknell SN7 4LT
      <svg viewBox="0 0 12 12" aria-hidden="true"><path d="M6 0.5a4 4 0 0 1 4 4C10 8 6 11.5 6 11.5S2 8 2 4.5a4 4 0 0 1 4-4zm0 2.3a1.7 1.7 0 1 0 0 3.4 1.7 1.7 0 0 0 0-3.4z"/></svg>
    </div>
  </div>
  <div class="tab tab-top"></div>

  <div class="watermark" role="img" aria-label="Faint watermark of a coach silhouette with a sprinting athlete"></div>

  <section class="letter">
    <p class="salutation">Dear Sir,</p>
    <p class="body">Lorem Ipsum is simply dummy text of the printing and typesetting industry. Lorem Ipsum has been the industry's standard dummy text ever since the 1500s, when an unknown printer took a galley of type and scrambled it to make a type specimen book. It has survived not only five centuries, but also the leap into electronic typesetting, remaining essentially unchanged. It was popularised in the 1960s with the release of Letraset sheets containing Lorem Ipsum passages, and more recently with desktop publishing software like Aldus PageMaker including versions of Lorem Ipsum.</p>
    <p class="body">Lorem Ipsum is simply dummy text of the printing and typesetting industry. Lorem Ipsum has been the industry's standard dummy text ever since the 1500s, when an unknown printer took a galley of type and scrambled it to make a type specimen book. It has survived not only five centuries, but also the leap into electronic typesetting, remaining essentially unchanged. It was popularised in the 1960s with the release of Letraset sheets containing Lorem Ipsum passages, and more recently with desktop publishing software like Aldus PageMaker including versions of Lorem Ipsum.</p>
    <p class="body">Lorem Ipsum is simply dummy text of the printing and typesetting industry. Lorem Ipsum has been the industry's standard dummy text ever since the 1500s, when an unknown printer took a galley of type and scrambled it to make a type specimen book.</p>
  </section>

  <div class="sign-off">
    <div class="sign-name">Your Name</div>
    <div class="signature" role="img" aria-label="Handwritten signature"></div>
    <div class="sign-role">CEO &nbsp;|&nbsp; Owner</div>
  </div>

  <div class="tab tab-bottom"></div>
  <div class="practitioner">
    <div class="practitioner-name">Derek Moss</div>
    <div class="credentials">Clinical Hypnotherapist<span class="sep">|</span>Hypnoanalyst<span class="sep">|</span>Mental Resilience Coach<span class="sep">|</span>Msc, Dip Phh</div>
  </div>

  <svg class="base-band" width="1102" height="20" viewBox="0 0 1102 20" aria-hidden="true">
    <polygon points="512,0 1102,0 1102,20 493,20" fill="var(--ink)"/>
  </svg>
</main>
</body>
</html>
```